Fenwick Ridge Accounting - New client package

I need a stationary package (presentation folder cover, welcome letter template/design, sample financial report template/design, business card and new logo) for my accounting business. I would like to see designs that use the color blue. Financial icons can be included in the design. The final design should be clean and communicate professionalism and the use of modern; user-friendly technology. Attached postcard files should help with overall design concept.

```html
<!DOCTYPE html>
<html lang="en">
<head>
<meta charset="utf-8">
<title>Fenwick Ridge Accounting – Business Card</title>
<link rel="stylesheet" href="https://fonts.googleapis.com/css2?family=Roboto:wght@400;500&family=Roboto+Condensed:wght@500&display=swap">
<style>
  :root {
    --stage: #181818;
    --brand-blue: #2e5c8a;
    --brand-blue-soft: #3a6a96;
    --paper: #f8f9fa;
    --edge-shadow: #9fb2c6;
    --ink-light: #ffffff;
  }
  * { box-sizing: border-box; margin: 0; padding: 0; }
  html, body {
    width: 1200px; height: 1200px; overflow: hidden;
    background: var(--stage);
    font-family: "Roboto", Arial, sans-serif;
  }
  .card {
    position: absolute; left: 318px; width: 562px; height: 340px;
    overflow: hidden;
  }
  .card--front { top: 251px; background: var(--brand-blue); }
  .card--back { top: 608px; background: var(--brand-blue); }

  .front-halo {
    position: absolute; left: 110px; top: -10px;
    width: 340px; height: 340px; border-radius: 50%;
    background: var(--brand-blue-soft);
  }
  .front-wordmark {
    position: absolute; left: 0; right: 0; top: 132px;
    text-align: center; color: var(--ink-light); font-weight: 500;
  }
  .front-wordmark .line-main { display: block; font-size: 38px; letter-spacing: 3px; line-height: 1; }
  .front-wordmark .line-sub { display: block; font-size: 22px; letter-spacing: 19px; margin-top: 8px; padding-left: 19px; line-height: 1; }

  .back-shape { position: absolute; inset: 0; }
  .holder {
    position: absolute; left: 34px; top: 46px; color: var(--ink-light);
  }
  .holder-name { font-family: "Roboto Condensed", Arial, sans-serif; font-weight: 500; font-size: 22px; }
  .holder-role { font-size: 14px; margin-top: 4px; }
  .contacts {
    position: absolute; left: 34px; top: 228px; list-style: none;
    color: var(--ink-light); font-size: 14.5px;
  }
  .contacts li { display: flex; align-items: center; height: 21px; }
  .contacts svg { width: 12px; height: 12px; margin-right: 10px; fill: var(--ink-light); }

  .brand-lockup {
    position: absolute; left: 300px; width: 262px; top: 94px;
    text-align: center; color: var(--brand-blue); font-weight: 500;
  }
  .brand-dot {
    width: 112px; height: 112px; border-radius: 50%;
    background: var(--brand-blue); margin: 0 auto 12px;
  }
  .brand-lockup .line-main { display: block; font-size: 20px; letter-spacing: 1.5px; line-height: 1.1; }
  .brand-lockup .line-sub { display: block; font-size: 12px; letter-spacing: 9px; padding-left: 9px; margin-top: 2px; }
</style>
</head>
<body>
  <section class="card card--front">
    <div class="front-halo"></div>
    <div class="front-wordmark">
      <span class="line-main">FENWICK RIDGE</span>
      <span class="line-sub">ACCOUNTING</span>
    </div>
  </section>

  <section class="card card--back">
    <svg class="back-shape" viewBox="0 0 562 340" preserveAspectRatio="none" aria-hidden="true">
      <path d="M330 0 Q262 170 330 340 L562 340 L562 0 Z" fill="var(--edge-shadow)"/>
      <path d="M330 0 Q272 170 340 340 L562 340 L562 0 Z" fill="var(--paper)"/>
    </svg>

    <div class="holder">
      <div class="holder-name">Aldous Penhale</div>
      <div class="holder-role">Managing Director</div>
    </div>

    <ul class="contacts">
      <li><svg viewBox="0 0 12 12"><path d="M1 4 Q6 0 11 4 L10 5.5 8 4.8 8 3.8 Q6 3 4 3.8 L4 4.8 2 5.5Z M3 6 H9 L10 11 H2Z"/></svg>1.800.555.0142</li>
      <li><svg viewBox="0 0 12 12"><path d="M0 2 H12 V10 H0Z M1 3 L6 7 11 3" fill="none" stroke="#fff" stroke-width="1.2"/></svg>info@fenwickridgeaccounting.com</li>
      <li><svg viewBox="0 0 12 12"><g fill="none" stroke="#fff" stroke-width="1"><circle cx="6" cy="6" r="5"/><ellipse cx="6" cy="6" rx="2.2" ry="5"/><path d="M1 6 H11 M2 3.5 H10 M2 8.5 H10"/></g></svg>www.fenwickridgeaccounting.com</li>
    </ul>

    <div class="brand-lockup">
      <div class="brand-dot"></div>
      <span class="line-main">FENWICK RIDGE</span>
      <span class="line-sub">ACCOUNTING</span>
    </div>
  </section>
</body>
</html>
```